Business Card Design for a Personal Trainer

I need a business card design for my job as a personal trainer. It should have a unique, modern and exclusive design. On the front there should be only my logo with my name and my job. 0162/3819204 Tobias Lendhart Wiesengrundweg 14 80417 Munich Germany The most important contact information is the web adress. it can be bigger than the rest, but its not necessary. The card should be 8,5cmx5,5cm big. Font: Roboto. Colors: black, white, gray, 56c1ff.

```html
<!DOCTYPE html>
<html lang="de">
<head>
<meta charset="utf-8">
<title>Tobias Lendhart – Personal Trainer Visitenkarte</title>
<link href="https://fonts.googleapis.com/css2?family=Roboto:wght@300;400;500;700&display=swap" rel="stylesheet">
<style>
  :root {
    --stage: #2e2e2e;
    --card-dark: #141414;
    --card-mid: #3c3c3c;
    --card-light: #5a5a5a;
    --white: #ffffff;
    --text-soft: #d6d6d6;
    --accent: #56c1ff;
  }
  * { margin: 0; padding: 0; box-sizing: border-box; }
  html, body {
    width: 1200px; height: 716px; overflow: hidden;
    background: var(--stage);
    font-family: "Roboto", Arial, sans-serif;
  }
  .stage {
    position: relative; width: 1200px; height: 716px;
    display: flex; align-items: center; justify-content: center; gap: 50px;
  }
  .card {
    position: relative; width: 500px; height: 324px;
    border-radius: 6px; overflow: hidden;
    box-shadow: 0 14px 30px rgba(0,0,0,.45);
  }
  .card--front {
    background: linear-gradient(135deg, var(--card-light) 0%, var(--card-mid) 45%, var(--card-dark) 100%);
  }
  .card--back {
    background: radial-gradient(ellipse at 40% 45%, var(--card-light) 0%, var(--card-mid) 40%, var(--card-dark) 100%);
  }
  .brand {
    position: absolute; display: flex; flex-direction: column; align-items: center;
    color: var(--white);
  }
  .card--front .brand { left: 50%; top: 50%; transform: translate(-50%, -50%); }
  .card--back .brand { left: 36px; top: 78px; }
  .brand__mark {
    width: 18px; height: 18px; background: var(--white); margin-bottom: 12px;
  }
  .brand__name {
    font-size: 23px; font-weight: 400; letter-spacing: 1px; text-transform: uppercase;
    line-height: 1;
  }
  .card--front .brand__name { font-size: 30px; }
  .brand__role {
    margin-top: 6px; padding-top: 4px; width: 100%;
    border-top: 1px solid var(--accent);
    font-size: 10px; font-weight: 300; letter-spacing: 3px; text-align: center;
    text-transform: uppercase; color: var(--text-soft);
  }
  .card--front .brand__role { font-size: 12px; letter-spacing: 4px; }
  .contact {
    position: absolute; left: 300px; top: 118px; color: var(--text-soft);
    font-size: 12.5px; font-weight: 300; line-height: 1.55;
  }
  .contact__name {
    color: var(--white); font-size: 15px; font-weight: 700; margin-bottom: 10px;
  }
  .contact__row { display: flex; align-items: center; gap: 7px; }
  .contact__icon { width: 11px; height: 11px; flex: none; }
  .website {
    position: absolute; left: 36px; bottom: 44px; color: var(--white);
    font-size: 24px; font-weight: 400; letter-spacing: .5px;
  }
</style>
</head>
<body>
<main class="stage">
  <section class="card card--front" aria-label="Vorderseite">
    <div class="brand">
      <span class="brand__mark"></span>
      <span class="brand__name">Tobias Lendhart</span>
      <span class="brand__role">Personal Trainer</span>
    </div>
  </section>

  <section class="card card--back" aria-label="Rückseite">
    <div class="brand">
      <span class="brand__mark"></span>
      <span class="brand__name">Tobias Lendhart</span>
      <span class="brand__role">Personal Trainer</span>
    </div>
    <div class="contact">
      <p class="contact__name">Tobias Lendhart</p>
      <p class="contact__row">
        <svg class="contact__icon" viewBox="0 0 12 12" aria-hidden="true"><path d="M2.5 1h2l1 3-1.3 1a6.5 6.5 0 0 0 2.8 2.8l1-1.3 3 1v2a1.5 1.5 0 0 1-1.5 1.5A9.5 9.5 0 0 1 1 2.5 1.5 1.5 0 0 1 2.5 1z" fill="#56c1ff"/></svg>
        0162/3819204
      </p>
      <p class="contact__row">
        <svg class="contact__icon" viewBox="0 0 12 12" aria-hidden="true"><rect x="1" y="2.5" width="10" height="7" rx="1" fill="none" stroke="#56c1ff" stroke-width="1.2"/><path d="M1.5 3l4.5 3.5L10.5 3" fill="none" stroke="#56c1ff" stroke-width="1.2"/></svg>
        t.lendhart@postfeld.de
      </p>
      <p>Wiesengrundweg 14</p>
      <p>80417 München</p>
    </div>
    <p class="website">www.tobiaslendhart.de</p>
  </section>
</main>
</body>
</html>
```